Sustainably Transforming Education

Company is education services based. early learning through adult and corporate. Focus is national government policy and program design and delivery alongside a research based and academically grounded set of approaches to planning, evaluation, and change management.I am looking for an innovative design position that aligns with the global agendas for innovation, creativity and collaboration at international and national policy levels (berulo is a name that reflects these qualities - colours need to reflect amythyst in some way). I also need a design that translates from a business card as 1 medium of interaction to a template that can work in word/powerpoint etc to support both stationery as well as a digital strategy across multiple channels (fb/twit/etc)There is no slogan/tag line for the company and their is no logo. I was looking to just leverage the name - have currently played around with various fonts (ending up with cuisine - all lowercase).

Industry/Entity Type

Adult

Contact Information for Business Card

name: berulo (all lowercase)Chairman: Andrew CrowMobile: +61 418 902 131Web: www.berulo.comemail: martin.pelly@berulo-example.com

Font styles to use
Script
Other font styles liked:
• cuisine

Colors
e34298
e667a6
33a6d7
aaaaaa

Requirements
Nice to have
• https://files.example-share.net/sh/qx7kw2hd91lzmnp/AAFr3tYbQeLp8VwZnKcDs2Hu?dl=0
• Link to the printwell templates used to begin this process....the one with the lines was about people intersecting (collaborating).....the organic shapes one more of a fluid feel of people coming together - the overall shape being largely spherical could represent a "global" feel.....anyway that is how I was thinking about these

```html
<!DOCTYPE html>
<html lang="en">
<head>
<meta charset="utf-8">
<title>berulo business card</title>
<link rel="stylesheet" href="https://fonts.googleapis.com/css2?family=Courgette&display=swap">
<style>
  :root {
    --backdrop: #ececec;
    --card: #ffffff;
    --amethyst: #8e5bb8;
    --blue: #33a6d7;
    --magenta: #e34298;
    --orchid: #e667a6;
    --edge: #2b2b2b;
    --brand: #1b86b3;
    --ink: #1c1c1c;
    --muted: #aaaaaa;
    --rule: #c9c9c9;
    --shade: #c6c7c9;
  }
  html, body {
    margin: 0;
    padding: 0;
    overflow: hidden;
  }
  body {
    width: 1200px;
    height: 1152px;
    background: var(--backdrop);
    position: relative;
  }
  .card {
    position: absolute;
    left: 162px;
    width: 875px;
    height: 500px;
    background: var(--card);
    box-shadow: 0 6px 18px rgba(0,0,0,0.12);
  }
  .card--contact { top: 50px; }
  .card--brand { top: 602px; }
  .card svg { display: block; }
  .wordmark,
  .person-name,
  .person-role,
  .contact-line {
    font-family: "Courgette", cursive;
  }
  .wordmark { fill: var(--brand); }
  .person-name { fill: var(--ink); }
  .person-role { fill: var(--muted); }
  .contact-line { fill: #ffffff; }
  .stripe-edge { stroke: var(--edge); }
  .stripe--amethyst { stroke: var(--amethyst); }
  .stripe--blue { stroke: var(--blue); }
  .stripe--magenta { stroke: var(--magenta); }
  .stripe--orchid { stroke: var(--orchid); }
  .stripe-fade { opacity: 0.35; }
  .name-rule { stroke: var(--rule); }
</style>
</head>
<body>

<section class="card card--contact" aria-label="Business card, contact side">
  <svg width="875" height="500" viewBox="0 0 875 500">
    <defs>
      <linearGradient id="fold-shade" x1="0" y1="0" x2="0" y2="1">
        <stop offset="0" stop-color="var(--shade)"/>
        <stop offset="1" stop-color="#ffffff"/>
      </linearGradient>
      <clipPath id="contact-clip"><rect width="875" height="500"/></clipPath>
    </defs>

    <g clip-path="url(#contact-clip)" fill="none" stroke-linejoin="miter" stroke-miterlimit="10">
      <polygon points="745,268 875,314 875,500 560,500" fill="url(#fold-shade)" stroke="none"/>

      <g class="stripe-fade" stroke-width="32">
        <line class="stripe--amethyst" x1="690" y1="95" x2="760" y2="-10"/>
        <line class="stripe--blue" x1="722" y1="110" x2="798" y2="-10"/>
        <line class="stripe--magenta" x1="754" y1="124" x2="836" y2="-10"/>
        <line class="stripe--orchid" x1="786" y1="138" x2="874" y2="-10"/>
      </g>

      <g class="stripe-edge" stroke-width="38">
        <polyline points="330,500 690,95 875,160"/>
        <polyline points="383,500 702,142 875,203"/>
        <polyline points="436,500 714,189 875,246"/>
        <polyline points="489,500 726,236 875,288"/>
      </g>

      <g stroke-width="32">
        <polyline class="stripe--amethyst" points="330,500 690,95 875,160"/>
        <polyline class="stripe--blue" points="383,500 702,142 875,203"/>
        <polyline class="stripe--magenta" points="436,500 714,189 875,246"/>
        <polyline class="stripe--orchid" points="489,500 726,236 875,288"/>
      </g>
    </g>

    <g dominant-baseline="central" font-size="17">
      <text class="contact-line" transform="translate(505 363) rotate(-48.4)">+61 427 315 086</text>
      <text class="contact-line" transform="translate(500 429) rotate(-48.4)" font-size="15">martin.pelly@berulo-example.com</text>
      <text class="contact-line" transform="translate(560 421) rotate(-48.4)" font-size="15">www.berulo-example.com</text>
    </g>

    <text class="wordmark" x="140" y="262" font-size="44">berulo</text>
    <line class="name-rule" x1="140" y1="280" x2="430" y2="280" stroke-width="1.2"/>
    <text class="person-name" x="152" y="318" font-size="30">Martin Pelly</text>
    <text class="person-role" x="154" y="346" font-size="17">Chairman</text>
  </svg>
</section>

<section class="card card--brand" aria-label="Business card, brand side">
  <svg width="875" height="500" viewBox="0 0 875 500">
    <defs>
      <clipPath id="brand-clip"><rect width="875" height="500"/></clipPath>
    </defs>
    <g clip-path="url(#brand-clip)" fill="none" stroke-width="34">
      <line class="stripe--amethyst" x1="322" y1="530" x2="638" y2="-30"/>
      <line class="stripe--blue" x1="372" y1="530" x2="688" y2="-30"/>
      <line class="stripe--magenta" x1="422" y1="530" x2="738" y2="-30"/>
      <line class="stripe--orchid" x1="472" y1="530" x2="788" y2="-30"/>
    </g>
    <text class="wordmark" x="120" y="290" font-size="84">berulo</text>
  </svg>
</section>

</body>
</html>
```